Vehicle Rental Hire in the Algarve - Portugal

We are opening a Vehicle Rental company in the Algarve - Portugal - this will attract both locals and Tourists visiting. So we want this website to capture the beautiful location we will be set in, along with the familiarity of a vehicle rental company. And to keep a colour scheme in Line with out Logo. We are Quenmira Vehicle Rental.

Industry/Entity Type

Vehicle Rental

Number of Pages Required

1 page

Requirements
Must have
• must be professional, and simple to use navigation bar - must also have a "make a reservation" box - similar to the screenshot attached - Under our logo it must read "Vehicle Rental"
Nice to have
• It needs to be in a colour scheme that fits in with our logo

```html
<!DOCTYPE html>
<html lang="en">
<head>
<meta charset="utf-8">
<title>Quenmira Vehicle Rental</title>
<link href="https://fonts.googleapis.com/css2?family=Roboto:wght@400;500;700&family=Ubuntu:wght@500&display=swap" rel="stylesheet">
<style>
:root{
  --red:#c8302a;
  --blue:#1b10e2;
  --ink:#111;
  --grey-bg:#bdbdbd;
  --field:#eef1f5;
  --text-grey:#777;
  --sun:#d9a35c;
  --dusk:#3a2a22;
}
*{margin:0;padding:0;box-sizing:border-box}
html,body{width:1200px;height:2339px;overflow:hidden;background:var(--grey-bg);font-family:'Roboto',sans-serif}
.stage{position:absolute;left:0;top:0;width:1322px;height:2576px;transform:scale(0.90772);transform-origin:0 0}
.screen{position:absolute;left:113px;width:1096px;background:#fff;overflow:hidden}
.abs{position:absolute}
.topbar{position:absolute;left:0;top:0;width:100%;height:30px;background:var(--red);color:#fff;font-size:12px}
.topbar .item{position:absolute;top:0;line-height:26px;display:flex;align-items:center;gap:6px}
.social{position:absolute;top:6px;width:17px;height:17px;border-radius:50%;background:var(--blue)}
.partner{text-decoration:underline}
.flag{width:13px;height:9px;background:linear-gradient(#fff 0 50%,var(--red) 50%);border:1px solid #fff}
.nav{position:absolute;left:0;top:30px;width:100%;height:55px;background:#fff}
.nav a{position:absolute;top:0;line-height:55px;font-size:13px;font-weight:500;color:var(--ink);text-decoration:none}
.logo-plate{position:absolute;left:464px;top:30px;width:168px;height:102px;z-index:3}
.logo-name{position:absolute;left:0;top:30px;width:168px;text-align:center;font-size:22px;font-weight:700;color:var(--blue);letter-spacing:.5px}
.logo-sub{position:absolute;left:0;top:60px;width:168px;text-align:center;font-size:10px;font-weight:500;color:var(--red);letter-spacing:2px}
.hero{position:absolute;left:0;width:100%;height:728px;
  background:linear-gradient(180deg,#c2ab8c 0%,var(--sun) 30%,#9a6a40 55%,#5a3c2c 78%,var(--dusk) 100%)}
.welcome{position:absolute;left:132px;top:102px;font-size:10px;font-weight:700;color:var(--ink)}
.headline{position:absolute;left:132px;top:128px;font-family:'Ubuntu',sans-serif;font-weight:500;font-size:29px;color:var(--ink);letter-spacing:.5px}
.headline .brand{color:var(--red)}
.lead{position:absolute;left:132px;top:180px;width:430px;font-size:14px;line-height:23px;color:var(--ink)}
.btn{position:absolute;display:flex;align-items:center;justify-content:center;gap:6px;background:var(--blue);color:#fff;font-weight:700;border-radius:24px}
.btn .dot{width:12px;height:12px;border-radius:50%;background:#fff;position:relative}
.btn .dot:after{content:"";position:absolute;left:4px;top:3px;border-left:5px solid var(--blue);border-top:3px solid transparent;border-bottom:3px solid transparent}
.panel{position:absolute;left:631px;top:166px;width:370px;height:562px;background:rgba(62,58,56,.78);border-top:4px solid var(--blue)}
.panel h2{position:absolute;left:0;top:22px;width:100%;text-align:center;color:#fff;font-size:19px;font-weight:700}
.label{position:absolute;font-size:12px;color:#fff;display:flex;align-items:center;gap:5px}
.label i{display:inline-block;width:8px;height:9px;background:var(--red);border-radius:2px}
.field{position:absolute;height:37px;background:var(--field);border-radius:2px;font-size:9.5px;color:#555;line-height:37px;padding-left:12px}
.field.select:after{content:"";position:absolute;right:14px;top:16px;border-top:4px solid #bbb;border-left:4px solid transparent;border-right:4px solid transparent}
.footer{position:absolute;left:0;width:100%;height:62px;background:#111;color:#fff;font-size:11px}
.copy{position:absolute;left:132px;top:0;line-height:62px}
.copy u{font-weight:500}
.subscribe{position:absolute;left:749px;top:15px;width:179px;height:31px;background:#fff;border-radius:16px 0 0 16px;font-size:8px;color:#666;line-height:31px;padding-left:24px}
.send{position:absolute;left:928px;top:15px;width:36px;height:31px;background:var(--blue);border-radius:0 16px 16px 0}
.services{position:absolute;left:0;top:814px;width:100%;height:564px;background:#fff}
.card{position:absolute;top:92px;width:263px;height:390px;background:#fff;box-shadow:0 2px 8px rgba(0,0,0,.14)}
.card .photo{position:absolute;left:6px;top:2px;width:251px;height:182px}
.card .icon{position:absolute;left:102px;top:153px;width:60px;height:60px;border-radius:50%;background:var(--red);border:3px solid #fff;display:flex;align-items:center;justify-content:center}
.card h3{position:absolute;top:227px;width:100%;text-align:center;font-size:15px;font-weight:500;color:var(--ink)}
.card p{position:absolute;top:256px;left:25px;width:213px;text-align:center;font-size:11px;line-height:19px;color:var(--text-grey)}
</style>
</head>
<body>
<div class="stage">

<section class="screen" style="top:98px;height:874px">
  <div class="topbar">
    <span class="item" style="left:77px"><svg width="11" height="8"><rect width="11" height="8" fill="#fff" opacity=".9"/><path d="M0 0l5.5 4L11 0" stroke="var(--red)" fill="none"/></svg>hello@quenmirarental.pt</span>
    <span class="social" style="left:339px"></span><span class="social" style="left:363px"></span><span class="social" style="left:387px"></span><span class="social" style="left:411px"></span>
    <span class="item" style="left:723px"><svg width="9" height="10"><path d="M2 0l2 3-1 1.5c1 1.5 2 2.5 3 3L7.5 6l2 2-1.5 2C4 9 1 5 0 1.5z" fill="#fff"/></svg>+351-289-555-014</span>
    <span class="item partner" style="left:890px">Partner Login</span>
    <span class="item" style="left:992px"><span class="flag"></span><b style="margin-left:4px">EN</b><svg width="8" height="5"><path d="M0 0h8L4 5z" fill="#fff"/></svg></span>
  </div>
  <nav class="nav">
    <a style="left:77px">Home</a><a style="left:144px">Fleet</a><a style="left:206px">Promotions</a><a style="left:307px">Extras &amp; Services</a>
    <a style="left:672px">About Us</a><a style="left:759px">Partners</a><a style="left:842px">Contacts</a><a style="left:928px">Rates&amp;Reservations</a>
  </nav>
  <div class="logo-plate">
    <svg class="abs" width="168" height="102"><path d="M0 0H168L156 102H12Z" fill="#fff"/></svg>
    <span class="logo-name">QUENMIRA</span>
    <span class="logo-sub">VEHICLE RENTAL</span>
  </div>
  <div class="hero" style="top:85px" role="img" aria-label="Red hatchback parked in a rental lot at sunset">
    <div class="welcome">Welcome To</div>
    <div class="headline"><span class="brand">QUENMIRA</span> VEHICLE RENTAL</div>
    <p class="lead">Lorem ipsum dolor sit amet, consectetur adipiscing elit, sed do eiusmod tempor incididunt ut labore et dolore magna.</p>
    <div class="btn" style="left:132px;top:254px;width:154px;height:46px;font-size:14px">Get Started <span class="dot"></span></div>
    <div class="panel">
      <h2>MAKE A RESERVATION</h2>
      <span class="label" style="left:34px;top:80px"><i></i>Pick up location</span>
      <div class="field select" style="left:34px;top:101px;width:295px">Choose Your Location</div>
      <span class="label" style="left:34px;top:159px"><i></i>Driver's age</span>
      <div class="field select" style="left:34px;top:180px;width:295px">Choose Your Age</div>
      <span class="label" style="left:34px;top:237px"><i></i>Vehicle Category</span>
      <div class="field select" style="left:34px;top:259px;width:295px">Choose Your Vehicle</div>
      <span class="label" style="left:34px;top:315px"><i></i>Pick up Date</span>
      <span class="label" style="left:186px;top:315px"><i></i>Hour</span>
      <div class="field" style="left:34px;top:337px;width:144px">DD:MM:YY</div>
      <div class="field" style="left:184px;top:337px;width:145px">DD:MM:YY</div>
      <span class="label" style="left:34px;top:395px"><i></i>Drop off date</span>
      <span class="label" style="left:186px;top:395px"><i></i>Hour</span>
      <div class="field" style="left:34px;top:416px;width:144px">DD:MM:YY</div>
      <div class="field" style="left:184px;top:416px;width:145px">DD:MM:YY</div>
      <div class="btn" style="left:125px;top:485px;width:120px;height:39px;font-size:14px">Search <span class="dot"></span></div>
    </div>
  </div>
  <footer class="footer" style="top:812px">
    <div class="copy">Copyright© 2024 &nbsp;<u>Quenmira Vehicle Rental</u> &nbsp;| &nbsp;All Rights Reserved</div>
    <div class="subscribe">Email Address</div>
    <div class="send"><svg width="36" height="31"><path d="M12 16l14-7-5 14-3-5z" fill="#fff"/></svg></div>
  </footer>
</section>

<section class="screen" style="top:1042px;height:1439px">
  <div class="topbar" style="height:29px">
    <span class="item" style="left:77px"><svg width="11" height="8"><rect width="11" height="8" fill="#fff" opacity=".9"/><path d="M0 0l5.5 4L11 0" stroke="var(--red)" fill="none"/></svg>hello@quenmirarental.pt</span>
    <span class="social" style="left:339px"></span><span class="social" style="left:363px"></span><span class="social" style="left:387px"></span><span class="social" style="left:411px"></span>
    <span class="item" style="left:723px"><svg width="9" height="10"><path d="M2 0l2 3-1 1.5c1 1.5 2 2.5 3 3L7.5 6l2 2-1.5 2C4 9 1 5 0 1.5z" fill="#fff"/></svg>+351-289-555-014</span>
    <span class="item partner" style="left:890px">Partner Login</span>
    <span class="item" style="left:992px"><span class="flag"></span><b style="margin-left:4px">EN</b><svg width="8" height="5"><path d="M0 0h8L4 5z" fill="#fff"/></svg></span>
  </div>
  <nav class="nav" style="top:29px">
    <a style="left:77px">Home</a><a style="left:144px">Fleet</a><a style="left:206px">Promotions</a><a style="left:307px">Extras &amp; Services</a>
    <a style="left:672px">About Us</a><a style="left:759px">Partners</a><a style="left:842px">Contacts</a><a style="left:928px">Rates&amp;Reservations</a>
  </nav>
  <div class="logo-plate" style="top:29px">
    <svg class="abs" width="168" height="102"><path d="M0 0H168L156 102H12Z" fill="#fff"/></svg>
    <span class="logo-name">QUENMIRA</span>
    <span class="logo-sub">VEHICLE RENTAL</span>
  </div>
  <div class="hero" style="top:84px;height:730px" role="img" aria-label="Red hatchback parked in a rental lot at sunset">
    <div class="welcome">Welcome To</div>
    <div class="headline"><span class="brand">QUENMIRA</span> VEHICLE RENTAL</div>
    <p class="lead">Lorem ipsum dolor sit amet, consectetur adipiscing elit, sed do eiusmod tempor incididunt ut labore et dolore magna.</p>
    <div class="btn" style="left:132px;top:254px;width:154px;height:46px;font-size:14px">Get Started <span class="dot"></span></div>
    <div class="panel" style="height:564px">
      <h2>MAKE A RESERVATION</h2>
      <span class="label" style="left:34px;top:80px"><i></i>Pick up location</span>
      <div class="field select" style="left:34px;top:101px;width:295px">Choose Your Location</div>
      <span class="label" style="left:34px;top:159px"><i></i>Driver's age</span>
      <div class="field select" style="left:34px;top:180px;width:295px">Choose Your Age</div>
      <span class="label" style="left:34px;top:237px"><i></i>Vehicle Category</span>
      <div class="field select" style="left:34px;top:259px;width:295px">Choose Your Vehicle</div>
      <span class="label" style="left:34px;top:315px"><i></i>Pick up Date</span>
      <span class="label" style="left:186px;top:315px"><i></i>Hour</span>
      <div class="field" style="left:34px;top:337px;width:144px">DD:MM:YY</div>
      <div class="field" style="left:184px;top:337px;width:145px">DD:MM:YY</div>
      <span class="label" style="left:34px;top:395px"><i></i>Drop off date</span>
      <span class="label" style="left:186px;top:395px"><i></i>Hour</span>
      <div class="field" style="left:34px;top:416px;width:144px">DD:MM:YY</div>
      <div class="field" style="left:184px;top:416px;width:145px">DD:MM:YY</div>
      <div class="btn" style="left:125px;top:485px;width:120px;height:39px;font-size:14px">Search <span class="dot"></span></div>
    </div>
  </div>

  <div class="services">
    <article class="card" style="left:127px">
      <div class="photo" role="img" aria-label="Rental agents inspecting a car in a showroom" style="background:linear-gradient(180deg,#c9ccd0,#7d8186)"></div>
      <div class="icon"><svg width="30" height="18" viewBox="0 0 30 18" fill="none" stroke="#fff" stroke-width="1.6"><path d="M3 12V9l3-5h18l3 5v3z"/><circle cx="8" cy="13" r="2.5"/><circle cx="22" cy="13" r="2.5"/><path d="M8 4l-1 4h16l-1-4"/></svg></div>
      <h3>Sed ut Perspiciatis</h3>
      <p>Lorem ipsum dolor sit amet, consectetur adipiscing elit, sed do eiusmod tempor labore et dolore magna aliqua.</p>
      <div class="btn" style="left:68px;top:330px;width:129px;height:39px;font-size:13px">Learn More <span class="dot"></span></div>
    </article>
    <article class="card" style="left:414px">
      <div class="photo" role="img" aria-label="Row of colourful trucks parked on a wet lot" style="background:linear-gradient(180deg,#8d9fb0,#3d6278)"></div>
      <div class="icon"><svg width="30" height="18" viewBox="0 0 30 18" fill="none" stroke="#fff" stroke-width="1.6"><path d="M3 12V9l3-5h18l3 5v3z"/><circle cx="8" cy="13" r="2.5"/><circle cx="22" cy="13" r="2.5"/><path d="M8 4l-1 4h16l-1-4"/></svg></div>
      <h3>Sed ut Perspiciatis</h3>
      <p>Lorem ipsum dolor sit amet, consectetur adipiscing elit, sed do eiusmod tempor labore et dolore magna aliqua.</p>
      <div class="btn" style="left:68px;top:330px;width:129px;height:39px;font-size:13px">Learn More <span class="dot"></span></div>
    </article>
    <article class="card" style="left:700px">
      <div class="photo" role="img" aria-label="Red, white and dark vans parked in a row" style="background:linear-gradient(180deg,#c4c6ca,#8e9093)"></div>
      <div class="icon"><svg width="30" height="18" viewBox="0 0 30 18" fill="none" stroke="#fff" stroke-width="1.6"><path d="M3 12V9l3-5h18l3 5v3z"/><circle cx="8" cy="13" r="2.5"/><circle cx="22" cy="13" r="2.5"/><path d="M8 4l-1 4h16l-1-4"/></svg></div>
      <h3>Sed ut Perspiciatis</h3>
      <p>Lorem ipsum dolor sit amet, consectetur adipiscing elit, sed do eiusmod tempor labore et dolore magna aliqua.</p>
      <div class="btn" style="left:68px;top:330px;width:129px;height:39px;font-size:13px">Learn More <span class="dot"></span></div>
    </article>
  </div>

  <footer class="footer" style="top:1378px;height:61px">
    <div class="copy">Copyright© 2024 &nbsp;<u>Quenmira Vehicle Rental</u> &nbsp;| &nbsp;All Rights Reserved</div>
    <div class="subscribe">Email Address</div>
    <div class="send"><svg width="36" height="31"><path d="M12 16l14-7-5 14-3-5z" fill="#fff"/></svg></div>
  </footer>
</section>

</div>
</body>
</html>
```